Talvex Health Artificial Intelligence MedTech Software Website Refresh

We need a new website (old one at www.talvex-health.example is no longer relevant) for our medtech software company using artificial intelligence to deliver higher quality, faster and more cost effective care in oncology. The audiences are both healthcare providers and health insurance payers. We've created an extensive outline to follow and have the old site still live for easy content use and repurposing. Our primary need is a great overhaul to look and feel. If we find a successful designer, we will need additional work done for graphics and other presentation projects.

Target Market(s)

Health care providers (doctors) and administrators plus health insurers

Industry/Entity Type

Medtech

Coding

Number of Pages Required

5+ page

Font styles to use
Other font styles liked:
• Roboto see Style Guide

Requirements
Must have
• See attached brief
Nice to have
• See attached brief. We like www.caremint.example and www.lumoradx.example as sites.
Should not have
• See attached brief

```html
<!DOCTYPE html>
<html lang="en">
<head>
<meta charset="utf-8">
<title>Talvex Health</title>
<link href="https://fonts.googleapis.com/css2?family=Poppins:ital,wght@0,300;0,400;0,500;0,600;0,700;1,300&family=Roboto:wght@400;500;700&display=swap" rel="stylesheet">
<style>
:root{
  --blue:#1a7cc8;
  --blue-dark:#1565b0;
  --sky:#2aa6e0;
  --ink:#1f1f1f;
  --muted:#666;
  --rule:#d8d8d8;
  --white:#fff;
}
*{box-sizing:border-box;margin:0;padding:0}
html,body{width:1200px;height:2901px;overflow:hidden;background:var(--white)}
body{position:relative;font-family:"Poppins",sans-serif;color:var(--ink)}
.abs{position:absolute}
.top-rule{left:0;top:0;width:1200px;height:3px;background:var(--sky)}
.header{left:0;top:3px;width:1200px;height:108px;border-bottom:1px solid var(--rule)}
.header-contact{left:110px;top:52px;font-family:"Roboto",sans-serif;font-size:14px;color:#333;display:flex;align-items:center;gap:7px}
.header-contact svg{width:12px;height:12px}
.brand{left:0;width:1200px;top:22px;text-align:center;font-family:"Poppins",sans-serif;font-weight:700;font-size:40px;color:var(--blue);line-height:1}
.brand-sub{left:0;width:1200px;top:72px;text-align:center;font-size:14px;letter-spacing:12px;color:var(--blue);font-weight:400}
.social{top:43px;width:30px;height:30px;border:1.6px solid #222;border-radius:50%}
.btn{display:flex;align-items:center;justify-content:center;border-radius:26px;background:var(--blue);color:var(--white);font-family:"Roboto",sans-serif;font-weight:700;font-size:14px}
.login{left:951px;top:34px;width:111px;height:49px}
.nav{left:0;top:111px;width:1200px;height:64px;display:flex;justify-content:center;gap:34px;align-items:center;font-family:"Roboto",sans-serif;font-weight:500;font-size:14px;color:#222}
.nav a{color:inherit;text-decoration:none;padding:6px 0;position:relative}
.nav a.active{color:var(--sky)}
.nav a.active::after{content:"";position:absolute;left:0;right:0;bottom:-2px;height:3px;background:var(--sky)}
.hero{left:0;top:175px;width:1200px;height:579px;background:radial-gradient(ellipse at 70% 20%,#4fb8f0 0%,#1c6fb9 40%,#0f3f74 100%)}
.hero-panel{left:208px;top:300px;width:783px;height:272px;background:rgba(18,50,100,.55);text-align:center;color:var(--white)}
.hero-panel h1{margin-top:38px;font-weight:700;font-size:52px;line-height:1}
.hero-panel p{margin-top:22px;font-size:15px;line-height:26px}
.hero-btn{left:523px;top:479px;width:155px;height:48px}
.welcome-img{left:142px;top:848px;width:427px;height:490px;border-radius:40px;border:1px solid #cfe3f3;background:linear-gradient(160deg,#f4f6f8 0%,#dfe7ee 55%,#b9d9f1 100%);box-shadow:0 10px 24px rgba(26,124,200,.15)}
.welcome{left:626px;top:845px;width:420px}
.eyebrow{font-weight:700;font-size:17px;letter-spacing:6px;color:#111}
.welcome h2{margin-top:10px;font-weight:400;font-size:33px;color:var(--sky);line-height:1.1}
.welcome p{margin-top:20px;font-size:15px;line-height:26px;color:var(--muted);text-align:justify}
.welcome p+p{margin-top:26px}
.learn{left:626px;top:1288px;width:155px;height:50px;gap:5px}
.card{display:flex;flex-direction:column;align-items:center;justify-content:center;color:var(--white);overflow:hidden;border-radius:3px;background:linear-gradient(120deg,#2b86cc 0%,#35a5df 60%,#2b86cc 100%)}
.card h3{font-weight:700;font-size:35px;line-height:1;margin-top:12px}
.card p{font-family:"Roboto",sans-serif;font-size:21px;margin-top:10px}
.card svg.icon{width:96px;height:96px}
.payer{left:111px;top:1432px;width:978px;height:306px}
.payer::before{content:"";position:absolute;left:290px;top:-60px;width:396px;height:396px;border-radius:50%;background:rgba(20,90,170,.18)}
.payer>*{position:relative}
.patient{left:111px;top:1750px;width:483px;height:306px}
.provider{left:606px;top:1750px;width:483px;height:306px}
.evidence-title{left:0;top:2142px;width:1200px;text-align:center;font-weight:700;font-size:35px;color:#222}
.cite{top:2234px;width:280px;text-align:center}
.cite h4{font-weight:600;font-size:16px;line-height:26px;color:var(--blue-dark)}
.cite hr{width:80px;margin:10px auto 8px;border:0;border-top:1px solid #777}
.cite p{font-style:italic;font-weight:300;font-size:14.5px;line-height:26px;color:#555}
.footer{left:0;top:2516px;width:1200px;height:302px;background:linear-gradient(120deg,#1c6dbe 0%,#2281cc 50%,#1a6cbb 100%);color:var(--white)}
.footer h5{font-weight:700;font-size:21px}
.f-col{position:absolute;font-size:15px;line-height:26px}
.email-field{left:695px;top:107px;width:395px;height:54px;border:1.5px solid var(--white);border-radius:28px;padding-left:30px;display:flex;align-items:center;font-size:13px}
.subscribe{left:695px;top:178px;width:155px;height:50px;background:var(--sky)}
.copy{left:0;top:2840px;width:1200px;text-align:center;font-size:15px;color:#333}
</style>
</head>
<body>
<div class="abs top-rule"></div>
<header class="abs header">
  <div class="abs header-contact">
    <svg viewBox="0 0 24 24"><path fill="#333" d="M6.6 10.8a15 15 0 006.6 6.6l2.2-2.2a1 1 0 011-.25 11.4 11.4 0 003.6.6 1 1 0 011 1V20a1 1 0 01-1 1A17 17 0 013 4a1 1 0 011-1h3.5a1 1 0 011 1c0 1.25.2 2.45.57 3.57a1 1 0 01-.25 1z"/></svg>
    (415) 555-0182 &nbsp;|&nbsp;
    <svg viewBox="0 0 24 24"><path fill="#333" d="M2 5h20v14H2z"/><path fill="#fff" d="M3 6l9 7 9-7v1l-9 7-9-7z"/></svg>
    info@talvex-health.example
  </div>
  <div class="abs brand">Talvex</div>
  <div class="abs brand-sub">HEALTH</div>
  <span class="abs social" style="left:771px" aria-label="Social link"></span>
  <span class="abs social" style="left:812px" aria-label="Social link"></span>
  <span class="abs social" style="left:852px" aria-label="Social link"></span>
  <span class="abs social" style="left:893px" aria-label="Social link"></span>
  <a class="abs btn login">&#9679;&nbsp;LOG IN</a>
</header>
<nav class="abs nav">
  <a class="active">HOME</a><a>TECHNOLOGY</a><a>COMPANY</a><a>EVIDENCE</a><a>CONTACT</a>
</nav>

<section class="abs hero" role="img" aria-label="Surgeons in a blue-lit operating room with digital interface overlays"></section>
<div class="abs hero-panel">
  <h1>TALVEX HEALTH</h1>
  <p>Talvex Health, Inc. is an expert team with the vision of improving oncology<br>treatment delivery, patient outcomes and cost effectiveness through the power of AI.</p>
</div>
<a class="abs btn hero-btn">GET STARTED</a>

<div class="abs welcome-img" role="img" aria-label="Doctor holding a stethoscope and tablet with floating AI and medical icons"></div>
<section class="abs welcome">
  <div class="eyebrow">WELCOME TO</div>
  <h2>TALVEX HEALTH, INC.</h2>
  <p>The problem(s) for providers: creating a treatment directive starts from scratch for every patient and is a time consuming iterative/back and forth process. Further, because there is little transparency to communicate patient-specific treatment needs to the payer, prior authorization is<br>a burden.</p>
  <p>The problem for payers: there is no transparency to the uniqueness of the patient so the process has costly delays to gather more information and align the treatment to what's best for the patient; often attempts to redirect care are unfruitful.</p>
</section>
<a class="abs btn learn">LEARN MORE <svg width="13" height="13" viewBox="0 0 20 20"><circle cx="10" cy="10" r="9" fill="#fff"/><path d="M7 5l5 5-5 5" stroke="#1a7cc8" stroke-width="2.5" fill="none"/></svg></a>

<div class="abs card payer">
  <svg class="icon" viewBox="0 0 96 96" fill="none" stroke="#fff" stroke-width="3"><circle cx="46" cy="20" r="15"/><circle cx="78" cy="34" r="9"/><circle cx="26" cy="68" r="15"/><circle cx="70" cy="70" r="15"/><path d="M38 33l-8 20M54 33l10 23M66 40l-8 20"/></svg>
  <h3>PAYER</h3>
  <p>$15M PMPY</p>
</div>
<div class="abs card patient">
  <svg class="icon" viewBox="0 0 96 96" fill="none" stroke="#fff" stroke-width="3"><circle cx="40" cy="30" r="16"/><path d="M12 90V74a16 16 0 0116-16h24a16 16 0 0116 16v16zM60 12c12 0 14 8 14 14s-4 10-8 12M66 40v18"/><circle cx="66" cy="64" r="6"/></svg>
  <h3>PATIENT</h3>
  <p>30 REDUCTION IN SIDE EFFECTS</p>
</div>
<div class="abs card provider">
  <svg class="icon" viewBox="0 0 96 96" fill="none" stroke="#fff" stroke-width="3"><circle cx="20" cy="22" r="10"/><circle cx="48" cy="16" r="10"/><circle cx="76" cy="22" r="10"/><path d="M14 70a14 14 0 010-28h68a14 14 0 010 28z"/><circle cx="48" cy="64" r="10"/><path d="M34 92a14 14 0 0128 0"/></svg>
  <h3>PROVIDER</h3>
  <p>$4K/PATIENT</p>
</div>

<h2 class="abs evidence-title">CLINICAL EVIDENCE</h2>
<article class="abs cite" style="left:134px">
  <h4>R. T. Calder, L.<br>M. Oswin, P. Dravek</h4><hr>
  <p>"Quantifying temporal trends and the impact of advances inradiation planning on heart and lung dose for lung cancer treatment using a machine learning model"</p>
</article>
<article class="abs cite" style="left:458px">
  <h4>Elin Varga, Toma R. Quist,<br>and Daniel P. Moray</h4><hr>
  <p>"Leveraging Artificial Intelligence (AI) clinical decision support software to improve treatment plan quality in head and neck cancer patients"</p>
</article>
<article class="abs cite" style="left:784px">
  <h4>Marcus Ilder, N. Fenwright,<br>V. Oakes</h4><hr>
  <p>"Predictive dosimetry using machine learning to guide dental management and extractions prior to head and neck radiotherapy"</p>
</article>

<footer class="abs footer">
  <h5 class="abs" style="left:111px;top:64px">CONTACT ME</h5>
  <div class="f-col" style="left:111px;top:108px">California Address:<br><br>2740 Harbor View Road<br>Suite 310<br>Belmont, CA 94002</div>
  <div class="f-col" style="left:454px;top:108px">Phone :<br>(415) 555-0182<br><br>Email Address :<br>info@talvex-health.example</div>
  <h5 class="abs" style="left:693px;top:64px">SUBSCRIBE TO GET MY NEWSLETTER</h5>
  <div class="abs email-field">Enter your email address</div>
  <a class="abs btn subscribe">SUBSCRIBE</a>
</footer>
<div class="abs copy">© Copyrights 2020 Company name | All Rights Reserved</div>
</body>
</html>
```